Copper Moth Bar & Grill Takeout Menu

Please create a takeout menu using the attached dine-in menu.
Take out menu size: Tri-Fold 11x17

Industry/Entity Type

Bar & Grill (Restaurant)

Colors

Designer to choose colors to be used in the design.

Requirements
Must have
• Phone number and website. "Order Online" "Order for Delivery"
Nice to have
• Area on the back of the menu to feature happy hour specials.

```html
<!DOCTYPE html>
<html lang="en">
<head>
<meta charset="utf-8">
<title>Copper Moth Bar &amp; Grill — Takeout Menu</title>
<link rel="stylesheet" href="https://fonts.googleapis.com/css2?family=Almendra+SC&family=Almendra:wght@700&family=Montserrat:wght@400;500;600;700;800&display=swap">
<style>
:root{
  --ink:#161616;
  --ink-2:#222;
  --violet:#3e2f9f;
  --violet-deep:#2f2386;
  --lemon:#e9da2b;
  --white:#ffffff;
  --soft:#d9d6ee;
  --stage:#e4e4e6;
}
*{box-sizing:border-box;margin:0;padding:0}
html,body{width:1200px;height:2400px;overflow:hidden;background:var(--stage)}
body{font-family:"Montserrat",sans-serif;color:var(--white)}
.canvas{width:1200px;height:2400px;display:flex;flex-direction:column;justify-content:center;gap:220px}
.spread{width:1200px;height:776px;display:flex}
.panel{width:400px;height:776px;padding:28px 26px;position:relative;overflow:hidden;display:flex;flex-direction:column}
.panel--dark{background:radial-gradient(ellipse at 30% 20%,#262626 0%,var(--ink) 70%)}
.panel--violet{background:radial-gradient(ellipse at 50% 30%,#4434aa 0%,var(--violet) 60%,var(--violet-deep) 100%)}
.section-title{font-family:"Almendra SC",serif;color:var(--lemon);font-size:30px;line-height:1;letter-spacing:.5px;margin-bottom:6px}
.section-title--sm{font-size:24px}
.note{font-size:9px;line-height:1.25;color:var(--white)}
.note strong{color:var(--lemon);font-weight:700}
.item{margin-top:9px}
.item-head{display:flex;align-items:center;gap:6px}
.item-name{font-size:11.5px;font-weight:700;color:var(--lemon);white-space:nowrap}
.rule{flex:1;height:1px;background:rgba(233,218,43,.55)}
.price{min-width:34px;height:15px;padding:0 5px;font-size:10px;font-weight:700;text-align:center;line-height:15px;background:var(--lemon);color:var(--ink)}
.price--violet{background:var(--violet);color:var(--white)}
.desc{font-size:9px;line-height:1.25;margin-top:3px;max-width:260px}
.tag{display:inline-block;font-size:8px;font-weight:700;padding:1px 4px;margin-left:3px}
.tag--cup{background:var(--violet);color:var(--white)}
.tag--bowl{background:var(--lemon);color:var(--ink)}
.veg{display:inline-block;width:6px;height:6px;border-radius:0 6px;background:#7bd13a;margin-left:3px}
.spicy{display:inline-block;width:6px;height:6px;border-radius:50%;background:#e53b2f;margin-left:2px}
.gap{height:20px}
/* lists */
.cols{display:flex;gap:18px}
.cols > div{flex:1}
.bullet-list{list-style:none;font-size:10px;line-height:1.28}
.bullet-list li::before{content:"";display:inline-block;width:5px;height:5px;border:1px solid var(--lemon);border-radius:50%;margin-right:6px;vertical-align:1px}
/* kids */
.kids{background:var(--lemon);color:var(--ink);margin-top:16px;padding:10px 12px;display:flex;height:150px}
.kids .section-title{color:var(--violet);font-size:25px}
.kids-list{width:170px}
.kids-row{display:flex;justify-content:space-between;align-items:center;font-size:9.5px;margin-top:5px}
.kids-row .price{background:var(--violet);color:var(--white);min-width:22px;height:13px;line-height:13px}
.art{display:block}
.art--kids{flex:1;margin-left:8px;border-radius:6px;background:linear-gradient(160deg,#f3a65a,#d4792f)}
.happy{margin:16px auto 0;border:2px solid var(--white);width:290px;height:66px;display:flex;align-items:center;padding:0 10px;gap:10px}
.happy-left{font-size:26px;line-height:.9;font-weight:500}
.happy-left b{font-weight:800}
.happy-bar{width:2px;height:48px;background:var(--white)}
.happy-right{color:var(--lemon);font-weight:800;font-size:24px;line-height:.95}
.contact{text-align:center;margin-top:14px}
.contact .section-title{font-family:"Almendra",serif;font-size:24px;margin-bottom:4px}
.icons{display:flex;justify-content:center;gap:6px;margin-bottom:4px}
.phone{font-size:19px;font-weight:500;margin-top:4px}
.web{font-family:"Almendra",serif;font-size:21px;margin-top:6px}
/* cover */
.cover{align-items:center;text-align:center;padding-top:34px}
.brand-mark{display:flex;align-items:center;gap:10px;font-family:"Almendra",serif;font-size:20px;color:var(--white)}
.brand-mark .dot{width:14px;height:14px;border-radius:50%;background:var(--white)}
.cover-title{font-family:"Almendra",serif;font-size:44px;line-height:1.02;margin-top:54px;color:var(--white)}
.cover-dots{color:var(--lemon);letter-spacing:3px;font-size:16px;margin-top:12px}
.cover-cta{font-family:"Almendra SC",serif;color:var(--lemon);font-size:29px;margin-top:4px}
.art--cover{position:absolute;left:0;bottom:0;width:400px;height:300px;background:linear-gradient(180deg,rgba(40,20,20,0) 0%,#5a2a22 35%,#c2574a 80%,#e07a6a 100%)}
/* salads */
.addons{font-size:8.5px;margin-top:8px;line-height:1.3}
.addons b{color:var(--lemon)}
.dressings{display:flex;background:var(--lemon);color:var(--ink);margin-top:10px;height:56px}
.dressings-label{width:16px;background:var(--violet);color:var(--lemon);writing-mode:vertical-rl;transform:rotate(180deg);font-size:7px;font-weight:800;text-align:center;letter-spacing:1px}
.dressings .cols{padding:6px 10px;gap:10px}
.dressings .bullet-list{font-size:9px;line-height:1.2}
.dressings .bullet-list li::before{border-color:var(--ink)}
.art--salads{position:absolute;left:0;bottom:0;width:400px;height:168px;background:linear-gradient(180deg,#7b4fa0 0%,#d4683a 55%,#e8a040 100%)}
/* starters */
.sub{font-size:10px;font-weight:700;color:var(--lemon);margin-top:12px}
.line{display:flex;align-items:center;gap:6px;font-size:8.5px;margin-top:3px}
.line .price{min-width:20px;height:11px;line-height:11px;font-size:8px}
.disclaimer{margin-top:auto;background:var(--violet);font-size:7.5px;line-height:1.3;padding:6px 60px 6px 10px;text-align:center;width:318px}
.art--mascot{position:absolute;right:12px;bottom:18px;width:54px;height:82px;border-radius:20px 20px 6px 6px;background:linear-gradient(180deg,#3a3a3a,#111)}
/* burgers */
.burger-head{display:flex;justify-content:flex-end;gap:20px;margin-top:10px;padding-right:4px}
.burger-head span{width:14px;height:14px;border-radius:50%}
.burger{display:flex;justify-content:space-between;margin-top:11px}
.burger .desc{max-width:170px}
.trio{display:flex;gap:8px;align-items:flex-start}
.trio .price{min-width:32px;height:13px;line-height:13px;font-size:8.5px}
.foot{font-size:8px;font-weight:700;color:var(--lemon);margin-top:auto}
</style>
</head>
<body>
<main class="canvas">

  <!-- Inside spread -->
  <section class="spread spread--outside">
    <article class="panel panel--dark">
      <h2 class="section-title">Soups &amp; Bowls</h2>
      <div class="item">
        <div class="item-head"><span class="item-name">Copper Moth Chili</span><span class="rule"></span><span class="tag tag--cup">CUP 6</span><span class="tag tag--bowl">BOWL 8</span></div>
        <p class="desc">Copper Moth Signature Chili with lean ground beef, black beans, and corn. Topped with cheddar cheese and green onion, served with tri-color tortilla chips.</p>
      </div>
      <div class="item">
        <div class="item-head"><span class="item-name">Southwestern Sweet Potato Soup<i class="veg"></i></span><span class="rule"></span><span class="tag tag--cup">CUP 6</span><span class="tag tag--bowl">BOWL 8</span></div>
        <p class="desc">A delicious mix of sweet potatoes, corn, bell peppers, and black beans, this vegan soup delivers top flavor and quality with every bowl. Served with tri-color tortilla chips.</p>
      </div>
      <div class="item">
        <div class="item-head"><span class="item-name">Ancient Grains Bowl</span><span class="rule"></span><span class="tag tag--cup">CUP 6</span><span class="tag tag--bowl">BOWL 8</span></div>
        <p class="desc">Quinoa, brown rice, kale and fresh spinach, with fire roasted portobello mushrooms, zucchini and red peppers. Topped with fresh avocado, and feta cheese. Served with Lemon Champagne Vinaigrette</p>
      </div>
      <div class="gap"></div>
      <h2 class="section-title">Other Handhelds</h2>
      <p class="note">All served with Hand Cut Fries or Sweet Potato Fries.<br><strong>Premium sides available for an up charge +2</strong></p>
      <div class="item">
        <div class="item-head"><span class="item-name">Cat Club</span><span class="rule"></span><span class="price">15</span></div>
        <p class="desc">Sliced whole wheat bread with roasted garlic aioli, grilled marinated chicken breast, provolone cheese bacon, lettuce and tomato.</p>
      </div>
      <div class="item">
        <div class="item-head"><span class="item-name">Southwest Melt</span><span class="rule"></span><span class="price">14</span></div>
        <p class="desc">Sliced whole wheat bread with roasted garlic aioli, 3 pepper colby jack, roasted red peppers and corn.</p>
      </div>
      <div class="item">
        <div class="item-head"><span class="item-name">What's Gouda?</span><span class="rule"></span><span class="price">14</span></div>
        <p class="desc">Sliced whole wheat bread with roasted garlic aioli smoked gouda and provolone cheeses, roasted red peppers and portobello mushrooms.</p>
      </div>
      <div class="item">
        <div class="item-head"><span class="item-name">Westover Melt</span><span class="rule"></span><span class="price">14</span></div>
        <p class="desc">Sliced whole wheat bread with roasted garlic aioli, zucchini, portobello mushrooms, red peppers, with melted brie and provolone cheeses</p>
      </div>
      <div class="gap"></div>
      <h2 class="section-title">Sides</h2>
      <p class="item-name" style="font-size:11px">Potato Salad <span style="color:#fff">&nbsp;$4</span> &nbsp;&nbsp;&nbsp;&nbsp;Fire Roasted Veggies <span style="color:#fff">&nbsp;$6</span></p>
      <p class="item-name" style="font-size:11px">Brown Rice, Quinoa, &amp; Kale Medley <span style="color:#fff">&nbsp;$5</span></p>
    </article>

    <article class="panel panel--violet">
      <div class="cols">
        <div>
          <h2 class="section-title section-title--sm">Cheeses</h2>
          <ul class="bullet-list"><li>Vermont Cheddar</li><li>Smoked Gouda</li><li>3-Pepper Colby Jack</li><li>Monterey Jack</li><li>Swiss</li><li>Brie</li><li>Provolone</li><li>American</li></ul>
        </div>
        <div>
          <h2 class="section-title section-title--sm">Condiments</h2>
          <ul class="bullet-list"><li>Horseradish Aioli</li><li>Chipotle Crema</li><li>Roasted Garlic Aioli</li><li>Citrus Aioli</li><li>Spicy Ketchup</li><li>Dijon Mustard</li><li>Yellow Mustard</li><li>Mayo</li><li>Ketchup</li></ul>
        </div>
      </div>
      <h2 class="section-title section-title--sm" style="margin-top:14px">Toppings</h2>
      <div class="cols">
        <ul class="bullet-list"><li>Bacon</li><li>Shrimp</li><li>Egg</li><li>Red Onion</li><li>White Onion</li><li>Portobello Mushrooms</li></ul>
        <ul class="bullet-list"><li>Roasted Corn</li><li>Roasted Red Peppers</li><li>Guacamole</li><li>Pico De Gallo</li><li>Fresh or Pickled Jalapenos</li></ul>
      </div>
      <div class="kids">
        <div class="kids-list">
          <h2 class="section-title">Kids Menu</h2>
          <p style="font-size:8px">All served with French Fries</p>
          <div style="margin-top:10px">
            <div class="kids-row"><span>Grilled Cheese</span><span class="price">8</span></div>
            <div class="kids-row"><span>Cheese Quesadilla</span><span class="price">8</span></div>
            <div class="kids-row"><span>Mac &amp; Cheese</span><span class="price">8</span></div>
            <div class="kids-row"><span>Chicken Tenders</span><span class="price">10</span></div>
          </div>
        </div>
        <div class="art art--kids" role="img" aria-label="Illustration of an orange striped tabby cat character"></div>
      </div>
      <div class="happy">
        <div class="happy-left">HAPPY<br><b>HOUR</b></div>
        <div class="happy-bar"></div>
        <div class="happy-right">FRIDAY<br><span style="font-size:20px">3PM–7PM</span></div>
      </div>
      <div class="contact">
        <h2 class="section-title">Contact Us</h2>
        <div class="icons">
          <svg width="16" height="16" viewBox="0 0 16 16" aria-label="Phone"><circle cx="8" cy="8" r="8" fill="#e9da2b"/><path d="M5 4.5l1.6-.4.9 2-1 .8a5 5 0 0 0 2.6 2.6l.8-1 2 .9-.4 1.6c-3.4.2-6.7-3.1-6.5-6.5z" fill="#3e2f9f"/></svg>
          <svg width="16" height="16" viewBox="0 0 16 16" aria-label="Website"><circle cx="8" cy="8" r="8" fill="#e9da2b"/><circle cx="8" cy="8" r="4.5" fill="none" stroke="#3e2f9f" stroke-width="1.1"/><path d="M3.5 8h9M8 3.5c-2 2.5-2 6.5 0 9M8 3.5c2 2.5 2 6.5 0 9" fill="none" stroke="#3e2f9f" stroke-width="1"/></svg>
        </div>
        <p class="phone">555-014-2290</p>
        <p class="web">www.coppermothgrill.com</p>
      </div>
    </article>

    <article class="panel panel--dark cover">
      <div class="brand-mark"><span class="dot"></span><span>Copper Moth</span></div>
      <h1 class="cover-title">Copper Moth<br><span style="color:#5a4cd6">Bar &amp; Grill</span></h1>
      <div class="cover-dots">•••••</div>
      <p class="cover-cta">Order Delivery</p>
      <div class="art art--cover" role="img" aria-label="Illustration of cartoon cats drinking and eating burgers at a bar table"></div>
    </article>
  </section>

  <!-- Menu spread -->
  <section class="spread spread--inside">
    <article class="panel panel--violet">
      <h2 class="section-title">Salads</h2>
      <div class="item"><div class="item-head"><span class="item-name">Combo Cat</span><span class="rule"></span><span class="price">11</span></div><p class="desc">Enjoy a side House and a cup of any soup.</p></div>
      <div class="item"><div class="item-head"><span class="item-name">Cat House Salad<i class="veg"></i></span><span class="rule"></span><span class="price">11</span></div><p class="desc">Spring lettuce mix, fresh red peppers, onion, cherry tomatoes, cucumber, and croutons. Served with Red Wine Vinaigrette.</p></div>
      <div class="item"><div class="item-head"><span class="item-name">Grilled Chicken Salad</span><span class="rule"></span><span class="price">15</span></div><p class="desc">Spring lettuce mix, grilled chicken breast, bacon, fresh red peppers, onions, tomatoes, cucumber and feta cheese. Served with Red Wine Vinaigrette</p></div>
      <div class="item"><div class="item-head"><span class="item-name">Grilled Shrimp Salad*</span><span class="rule"></span><span class="price">16</span></div><p class="desc">Spring lettuce mix, garlic Roasted Shrimp, roasted corn, pico de gallo fresh avocado, Served with Lemon Champagne Vinaigrette</p></div>
      <div class="item"><div class="item-head"><span class="item-name">Goat Cheese Salad<i class="veg"></i></span><span class="rule"></span><span class="price">16</span></div><p class="desc">Spring lettuce mix, fried goat cheese, fresh red peppers, cranberries, white onions, and cherry tomatoes. Served with Lemon Champagne Vinaigrette.</p></div>
      <div class="item"><div class="item-head"><span class="item-name">The Skinny Cat<i class="veg"></i></span><span class="rule"></span><span class="price">14</span></div><p class="desc">Spring lettuce mix, sliced apple, sun dried cranberries, roasted corn, cherry tomatoes, and feta cheese. Served with Balsamic Vinaigrette</p></div>
      <div class="item"><div class="item-head"><span class="item-name">Small House Salad<i class="veg"></i></span><span class="rule"></span><span class="price">6</span></div></div>
      <p class="addons"><b>Add:</b><br><b>Grilled Chicken 5</b> &nbsp;&nbsp;&nbsp;&nbsp;&nbsp;&nbsp;&nbsp;&nbsp;&nbsp;&nbsp;<b>Garlic Roasted Shrimp 5</b><br><b>Fried Goat Cheese 4</b></p>
      <div class="dressings">
        <div class="dressings-label">DRESSINGS</div>
        <div class="cols">
          <ul class="bullet-list"><li>Balsamic Vinaigrette</li><li>Caesar</li><li>Red Wine Vinaigrette</li><li>Honey-Mustard</li></ul>
          <ul class="bullet-list"><li>Lemon</li><li>Champagne Vinaigrette</li><li>Ranch</li><li>Blue Cheese</li></ul>
        </div>
      </div>
      <div class="art art--salads" role="img" aria-label="Illustration of cartoon cats sharing a meal at a wooden table"></div>
    </article>

    <article class="panel panel--dark">
      <h2 class="section-title">Starters</h2>
      <p class="sub" style="margin-top:4px">TORTILLA CHIPS</p>
      <div class="line"><span>with House-made Salsa Verde<i class="veg"></i><i class="spicy"></i></span><span class="rule"></span><span class="price">7</span></div>
      <div class="line"><span>with House-made Fire Roasted Salsa<i class="veg"></i></span><span class="rule"></span><span class="price">7</span></div>
      <div class="line"><span>with Guacamole &amp; Pico De Gallo<i class="veg"></i></span><span class="rule"></span><span class="price">8</span></div>
      <div class="line"><span>with Queso<i class="veg"></i></span><span class="rule"></span><span class="price">8</span></div>
      <div class="line"><span>with Chili con Queso</span><span class="rule"></span><span class="price">9</span></div>
      <div class="item-head" style="margin-top:12px"><span class="sub" style="margin:0">WINGS</span><span class="rule"></span><span class="price price--violet">14</span></div>
      <p class="desc">8 pieces<br>Flash-fried to a crispy golden brown and tossed in your choice of sauce. Choose from our Signature Hot, or Mild Sauce, or BBQ. Your choice of ranch or blue cheese.</p>
      <p class="sub">QUESADILLAS</p>
      <div class="line"><span>Cheddar and Monterey Jack Cheese<i class="veg"></i></span><span class="rule"></span><span class="price">12</span></div>
      <div class="line"><span>Pulled Marinated Chicken &amp; Cheese</span><span class="rule"></span><span class="price">16</span></div>
      <div class="line"><span>Fire Roasted Vegetables &amp; Cheese<i class="veg"></i></span><span class="rule"></span><span class="price">14</span></div>
      <div class="line"><span>Garlic Roasted Shrimp &amp; Cheese</span><span class="rule"></span><span class="price">16</span></div>
      <p class="desc" style="margin-top:6px">All quesadillas are stuffed with roasted red peppers, black beans and your choice below. Served with guacamole, pico de gallo, and chipotle crema on the side.</p>
      <p class="sub">CLAW-FULL NACHOS</p>
      <p class="desc">Tortilla chips, melted white queso, Cheddar and Monterey Jack cheeses, pico de gallo, guacamole, chipotle sour cream, jalapenos, black beans, &amp; green onions.</p>
      <div class="line" style="margin-top:5px"><span>Copper Moth Chili Nachos</span><span class="rule"></span><span class="price">14</span></div>
      <div class="line"><span>Pulled Chicken Nachos</span><span class="rule"></span><span class="price">16</span></div>
      <div class="line"><span>Garlic Roasted Shrimp</span><span class="rule"></span><span class="price">16</span></div>
      <div class="line"><span>Fire Roasted Vegetables Nachos<i class="veg"></i></span><span class="rule"></span><span class="price">14</span></div>
      <p class="sub">FRENCH FRIES</p>
      <p class="desc">Served with our house made Garlic Aioli and Spicy Ketchup.</p>
      <div class="line"><span>Fries Only<i class="veg"></i></span><span class="rule"></span><span class="price">7</span></div>
      <div class="line"><span>Sweet Potato Fries</span><span class="rule"></span><span class="price">7</span></div>
      <div class="line"><span>Cheddar-Jack Cheese Fries</span><span class="rule"></span><span class="price">8</span></div>
      <div class="line"><span>Cheddar-Jack Cheese, Bacon Fries</span><span class="rule"></span><span class="price">9</span></div>
      <div class="line"><span>Chili Cheese Fries</span><span class="rule"></span><span class="price">10</span></div>
      <div class="disclaimer">*The consumption of raw or undercooked eggs, meat, poultry, seafood or shellfish may contribute to food borne illness, especially if you have a medical condition.<br><i class="veg"></i> Vegetarian &nbsp; <i class="spicy"></i> Spicy</div>
      <div class="art art--mascot" role="img" aria-label="Illustration of a small black and white cat mascot"></div>
    </article>

    <article class="panel panel--dark">
      <h2 class="section-title" style="font-size:27px;line-height:1.05">Gourmet Burgers<br><span style="color:#5a4cd6">&amp; Sandwiches</span></h2>
      <p class="note" style="margin-top:6px">Start with your style and then choose your protein. Our burgers are house made and cooked to your temperature. Our Fresh grilled chicken breast is marinated in house and cooked to perfection. Keep it vegetarian by choosing a vegetarian style along with the Quinoa Lentil Burger. All are served on a potato bun with lettuce, tomato, onion, and your choice of hand cut fries or sweet potato fries. <strong>Premium sides available for an up charge + $2</strong></p>
      <p class="foot" style="margin-top:12px">GLUTEN-FREE BUN AVAILABLE UPON REQUEST | $2</p>
      <div class="burger-head">
        <span style="background:#f1c6d8" role="img" aria-label="Beef"></span>
        <span style="background:#f0a64a" role="img" aria-label="Chicken"></span>
        <span style="background:#7bd13a" role="img" aria-label="Vegetarian"></span>
      </div>
      <div class="burger"><div><span class="item-name">Calico Cat<i class="veg"></i></span><p class="desc">Roasted red peppers, red onions, brie cheese, and horseradish aioli.</p></div><div class="trio"><span class="price">15.00*</span><span class="price price--violet">14.00</span><span class="price">13.00</span></div></div>
      <div class="burger"><div><span class="item-name">Tiger Cat</span><p class="desc">Cheddar, Monterey Jack, and Provolone</p></div><div class="trio"><span class="price">15.00*</span><span class="price price--violet">14.00</span><span class="price">13.00</span></div></div>
      <div class="burger"><div><span class="item-name">Cat Scratch Fever<i class="veg"></i></span><p class="desc">Guacamole, 3 pepper colby jack, pico de gallo, and chipotle mayo.</p></div><div class="trio"><span class="price">15.50*</span><span class="price price--violet">14.50</span><span class="price">13.50</span></div></div>
      <div class="burger"><div><span class="item-name">The Fat Cat<i class="veg"></i></span><p class="desc">Fried egg*, bacon, cheddar cheese, and garlic aioli.</p></div><div class="trio"><span class="price">16.00*</span><span class="price price--violet">15.00</span><span class="price">14.00</span></div></div>
      <div class="burger"><div><span class="item-name">Tobby Cat</span><p class="desc">Melted brie cheese, sliced apple, and citrus aioli.</p></div><div class="trio"><span class="price">16.50*</span><span class="price price--violet">15.50</span><span class="price">14.50</span></div></div>
      <div class="burger"><div><span class="item-name">The Sphynx</span><p class="desc">Portobello mushrooms, roasted red peppers, smoked gouda cheese, and roasted garlic aioli.</p></div><div class="trio"><span class="price">16.50*</span><span class="price price--violet">15.50</span><span class="price">14.50</span></div></div>
      <div class="burger"><div><span class="item-name">Maine Coon</span><p class="desc">Grilled shrimp*, roasted corn, swiss cheese, and roasted garlic aioli.</p></div><div class="trio"><span class="price">16.50*</span><span class="price price--violet">15.50</span><span class="price">14.50</span></div></div>
      <div class="burger"><div><span class="item-name">Alley Cat</span><p class="desc">Whats up your alley? Choose a cheese, condiment and one</p></div><div class="trio"><span class="price">14.00*</span><span class="price price--violet">13.00</span><span class="price">12.00</span></div></div>
      <p class="foot">TOPPINGS: ADDITIONAL TOPPINGS $1 | BACON, EGG, SHRIMP - $2</p>
    </article>
  </section>

</main>
</body>
</html>
```